Fitness Equipment & Service

I want to make the card eye catching and fun. We are called Corvane Motion Limited and we are based in Wales. We sell, install and service all types of fitness equipment from Skipping ropes, right through the Dumbbells, Kettle bells and Barbells through to state of the art Treadmills, Running Machines and Strength Equipment. We also design and install changing room furniture and lockers.

TYPOGRAPHY
We would like to use Futrura. Futura has an appearance of efficiency and forwardness. The typeface is derived
from simple geometric forms (near-perfect circles, triangles and squares) and is based on strokes of
near-even weight, which are low in contrast. This is most visible in the almost perfectly round stroke of
the o, which is nonetheless slightly ovoid.
The lowercase has tall ascenders, which rise above the cap line. The uppercase
characters present proportions similar to those of classical Roman capitals.

TYPOGRAPHIC CONSIDERATIONS
No Strike though
No Horizontal Scaling
No Drop Shadows
No Effects
Never use less than 120% Leading

OUR CORPORATE COLOURS
BRAND GUIDELINES
We were thinking that our primary colour palette consists of the Acid Green (Pantone 382) and Process Black.

We work closely with tquarly Ltd and would like to include their name on the card somewhere. I have attached images of the other brands that we work with as an idea or the small icons I have included that illustrate what we do?. I have very kindly been given permission to use any of the images off the files that I have included below, so I hope these help. I will include these below. I would be open to suggestions if it made the card more striking Can you do it?
Updates

Hi All, Just wanted to add a few thoughts but you are the guys with the creative visions (thats why are here) We are based in Wales, UK and we would be open to lots of different ideas on a theme but must be eye catching, Bold and FUN. If you can or think that the Welsh or any dragon could be put in there then go for it (its not a must have) We have also added some ideas for colour but again its over to you!! GO FOR IT ! Thanks and look forward to your visions! Owen

Hi All, Just thought I would sen through the contact details that need to be on the card. (if you want to play around with icons instead of the wording twitter, Facebook, go for it): Corvane Motion Limited Owen Pritchard Managing Director Mob: +44 (0)7582 913 406 e-mail: sales@corvanemotion.co.uk Web: Corvanemotion.co.uk twitter: @motionLetterbin Facebook: Corvane Motion Limited

```html
<!DOCTYPE html>
<html lang="en">
<head>
<meta charset="utf-8">
<title>Corvane Motion Limited – Business Card</title>
<link rel="stylesheet" href="https://fonts.googleapis.com/css2?family=Jost:wght@600&family=Source+Sans+3:wght@400;600&display=swap">
<style>
  :root {
    --backdrop: #e4e5e7;
    --paper: #f6f6f7;
    --navy: #1b2a5a;
    --navy-deep: #14224b;
    --royal: #2f57a6;
    --gold: #c8973a;
    --ink: #3b3f4a;
    --tile-night: #1d3a5c;
    --tile-ocean: #2b7ec1;
    --tile-sky: #4aa3d6;
    --tile-deep: #1c3655;
    --tile-steel: #6d8fa6;
    --tile-slate: #7c95a8;
    --tile-sea: #1e5e8c;
    --tile-strip-mid: #2a6fa8;
    --tile-strip-low: #5a8db0;
    --white: #ffffff;
  }
  * { margin: 0; padding: 0; box-sizing: border-box; }
  html, body { width: 1105px; height: 1200px; overflow: hidden; }
  body { background: var(--backdrop); position: relative; font-family: "Source Sans 3", Arial, sans-serif; }

  .card { position: absolute; left: 180px; width: 746px; height: 426px; overflow: hidden; }

  /* Front */
  .card-front { top: 119px; background: var(--paper); color: var(--ink); }
  .brand-mark { position: absolute; left: 553px; top: 40px; width: 130px; height: 130px; border-radius: 50%;
    background: radial-gradient(circle at 45% 40%, var(--royal), var(--navy-deep)); }
  .brand-name { position: absolute; right: 38px; top: 186px; width: 220px; text-align: right;
    font-weight: 600; font-size: 15px; line-height: 1.2; letter-spacing: 0.5px; color: var(--navy); }
  .edge-accent { position: absolute; left: -10px; top: 213px; width: 20px; height: 62px; border-radius: 50%;
    background: linear-gradient(var(--royal), var(--navy)); }
  .person-name { position: absolute; left: 39px; top: 212px; font-size: 31px; font-weight: 600; line-height: 1.2; color: var(--navy); }
  .person-role { position: absolute; left: 39px; top: 250px; font-size: 21px; line-height: 1.2; color: var(--gold); }
  .divider { position: absolute; left: 39px; width: 674px; top: 287px; height: 2px; background: var(--gold); }
  .contact-list { position: absolute; left: 39px; top: 302px; list-style: none; }
  .contact-list li { display: flex; align-items: center; height: 28.5px; font-size: 19.5px; line-height: 1.2; }
  .contact-list svg { width: 18px; height: 18px; margin-right: 13px; fill: var(--navy); }
  .social-links { position: absolute; right: 35px; top: 306px; display: flex; gap: 5px; }
  .social-links span { width: 21px; height: 21px; background: var(--navy); }
  .address { position: absolute; right: 35px; top: 333px; text-align: right; font-size: 19.5px; line-height: 1.32; }
  .base-band { position: absolute; left: 0; bottom: 0; width: 100%; height: 13px; display: flex; }
  .base-band .band-navy { flex: 0 0 605px; background: linear-gradient(90deg, var(--navy), var(--royal) 70%, var(--navy)); }
  .base-band .band-gold { flex: 1; background: linear-gradient(90deg, #8d6424, var(--gold), #f0d089, var(--gold)); }

  /* Back */
  .card-back { top: 637px; display: grid; grid-template-columns: 29px repeat(5, 1fr); grid-template-rows: repeat(3, 1fr); }
  .tile { display: flex; align-items: center; justify-content: center; }
  .tile svg { width: 72px; height: 72px; fill: none; stroke: var(--white); stroke-width: 6; stroke-linejoin: round; stroke-linecap: round; }
  .tile-photo { background: linear-gradient(160deg, #22476f, #3c76a8 55%, #1a3556); }
  .partner-panel { grid-column: 2 / 4; grid-row: 2; position: relative; justify-content: flex-start; }
  .partner-name { padding-left: 21px; font-family: "Jost", Arial, sans-serif; font-weight: 600; font-size: 38px;
    line-height: 1.2; letter-spacing: 1px; color: var(--white); }
</style>
</head>
<body>

<section class="card card-front">
  <div class="brand-mark"></div>
  <div class="brand-name">CORVANE MOTION LIMITED</div>
  <div class="edge-accent"></div>
  <h1 class="person-name">OWEN PRITCHARD</h1>
  <p class="person-role">Managing Director</p>
  <div class="divider"></div>
  <ul class="contact-list">
    <li><svg viewBox="0 0 20 20"><path d="M5 1h10v18H5z M7 3v12h6V3z" fill-rule="evenodd"/></svg>+44 (0)7582 913 406</li>
    <li><svg viewBox="0 0 20 20"><path d="M1 4h18v12H1z M2.5 5.5l7.5 6 7.5-6" fill-rule="evenodd"/></svg>sales@corvanemotion.co.uk</li>
    <li><svg viewBox="0 0 20 20"><circle cx="10" cy="10" r="9"/></svg>Corvanemotion.co.uk</li>
  </ul>
  <div class="social-links"><span></span><span></span></div>
  <address class="address" style="font-style:normal">2318 Linden Row<br>Carrow Bay, Wales CF41 2TN</address>
  <div class="base-band"><div class="band-navy"></div><div class="band-gold"></div></div>
</section>

<section class="card card-back">
  <!-- row 1 -->
  <div class="tile" style="background:var(--tile-night)"></div>
  <div class="tile tile-photo" role="img" aria-label="Gym photograph with exercise bike icon"></div>
  <div class="tile" style="background:var(--tile-ocean)">
    <svg viewBox="0 0 100 100"><rect x="10" y="18" width="80" height="52" rx="3"/><path d="M50 70v12M34 84h32"/><circle cx="50" cy="44" r="14"/><path d="M36 44h28M50 30v28"/></svg>
  </div>
  <div class="tile" style="background:var(--tile-sky)" role="img" aria-label="Floor plan icon"></div>
  <div class="tile" style="background:var(--tile-ocean)" role="img" aria-label="Treadmill icon"></div>
  <div class="tile" style="background:var(--tile-night)">
    <svg viewBox="0 0 100 100"><path d="M14 38v24M24 30v40M76 30v40M86 38v24M24 50h52"/></svg>
  </div>

  <!-- row 2 -->
  <div class="tile" style="background:var(--tile-strip-mid)"></div>
  <div class="tile tile-photo partner-panel" role="img" aria-label="Gym interior photograph"><span class="partner-name">TQUARLY</span></div>
  <div class="tile" style="background:var(--tile-deep)">
    <svg viewBox="0 0 100 100"><rect x="24" y="8" width="24" height="84"/><rect x="52" y="8" width="24" height="84"/><path d="M24 36h24M24 64h24M52 50h24"/></svg>
  </div>
  <div class="tile" style="background:var(--tile-sky)">
    <svg viewBox="0 0 100 100"><rect x="26" y="10" width="48" height="80" rx="5"/><rect x="34" y="20" width="32" height="22"/><path d="M36 56h4M48 56h4M60 56h4M36 68h4M48 68h4M60 68h4M36 80h4M48 80h4M60 80h4"/></svg>
  </div>
  <div class="tile" style="background:var(--tile-steel)" role="img" aria-label="Group class screen icon"></div>

  <!-- row 3 -->
  <div class="tile" style="background:var(--tile-strip-low)"></div>
  <div class="tile" style="background:var(--tile-sea)" role="img" aria-label="Weight bench icon"></div>
  <div class="tile" style="background:var(--tile-ocean)" role="img" aria-label="Delivery van icon"></div>
  <div class="tile tile-photo" role="img" aria-label="Photograph with boxing gloves icon"></div>
  <div class="tile" style="background:var(--tile-slate)">
    <svg viewBox="0 0 100 100"><path d="M34 40c-4-10-2-26 16-26s20 16 16 26"/><circle cx="50" cy="62" r="26"/></svg>
  </div>
  <div class="tile" style="background:var(--tile-sea)">
    <svg viewBox="0 0 100 100"><circle cx="50" cy="56" r="30"/><path d="M44 12h12M50 12v14M50 56l12-12"/></svg>
  </div>
</section>

</body>
</html>
```